Craft Beer Company

We need a web design for our Tampa based craft beer company that shows and tells what we are about and our products, up and coming beers, events and happenings. Must has a verify age by selecting yes or no to "are you 21 years or older.. have logos and product labels etc... currently have Plimtora.com a our website, thats under construction.
Reason: more time to be thorough
Target Market(s)
Craft Beer Enthusiasts , Craft Beer Community
Industry/Entity Type
Construction
Requirements
Must have
- The pages on the site should have, about us, events, our beer, store for e-commerce
being that we are set up with Plimtora.com I would like to contineu to use them, unless there is another option available. We have the domain there.

```html
<!DOCTYPE html>
<html lang="en">
<head>
<meta charset="utf-8">
<title>Harborline Brew Co</title>
<link href="https://fonts.googleapis.com/css2?family=Philosopher&family=Open+Sans:wght@400;600&display=swap" rel="stylesheet">
<style>
:root{
  --cream:#f1e7dd;
  --cream-dark:#e9dccf;
  --forest:#1b2a1a;
  --forest-deep:#142014;
  --lime:#8dc63f;
  --ink:#2b2b2b;
  --muted:#6b6b6b;
  --link:#3b5a99;
  --white:#ffffff;
}
*{margin:0;padding:0;box-sizing:border-box}
html,body{width:717px;height:1200px;overflow:hidden}
body{position:relative;background:var(--cream);font-family:"Open Sans",Arial,sans-serif;color:var(--ink)}
.abs{position:absolute}
.heading{font-family:"Philosopher","Trebuchet MS",sans-serif;font-weight:400}

/* header */
.topbar{left:0;top:0;width:717px;height:35px;background:var(--cream-dark)}
.nav{left:0;top:35px;width:717px;height:26px;background:var(--forest);border-top:2px solid #2d4a2a;border-bottom:2px solid #2d4a2a}
.nav a{position:absolute;top:0;height:22px;line-height:22px;color:#e8e8e8;font-size:7px;letter-spacing:.6px;text-decoration:none}
.nav a.active{background:var(--lime);color:var(--forest);padding:0 10px}
.brand{left:323px;top:3px;width:72px;height:72px;border-radius:50%;background:var(--lime);border:3px solid var(--forest);display:flex;align-items:center;justify-content:center;text-align:center}
.brand span{font-family:"Open Sans",sans-serif;font-weight:600;font-size:8px;line-height:10px;color:var(--forest)}

/* hero */
.hero{left:0;top:68px;width:717px;height:298px;background:linear-gradient(180deg,#2b2236 0%,#3d2c3a 55%,#4a3422 80%,#1f1a17 100%)}
.hero-product{left:70px;top:58px;width:270px;height:196px;background:radial-gradient(ellipse at 40% 60%,#c99a2e 0%,#6b4a1c 55%,rgba(60,40,20,0) 80%)}
.hero-title{left:350px;top:121px;width:310px;color:var(--white);font-size:13.5px;line-height:18px}
.hero-sub{left:350px;top:162px;width:300px;color:#ddd;font-size:8.5px;line-height:14px}
.arrow{width:14px;height:28px}

/* welcome */
.section-title{width:717px;text-align:center;font-size:16px;color:var(--ink)}
.welcome-text{left:66px;top:410px;width:585px;text-align:center;font-size:6.3px;line-height:15px;color:#333}

.beers{left:58px;top:501px;width:600px;height:101px;background:var(--white);box-shadow:0 6px 6px -2px rgba(0,0,0,.5)}
.beer{position:absolute;top:0;width:195px;height:101px}
.beer .bottle{position:absolute;left:18px;top:0;width:20px;height:84px;border-radius:6px 6px 3px 3px;background:linear-gradient(180deg,#2a1a10,#5a3a1c 50%,#2a1a10)}
.beer h3{position:absolute;left:58px;top:16px;font-size:8.5px;color:var(--ink)}
.beer .rule{position:absolute;left:58px;top:35px;width:98px;height:1px;background:#ccc}
.beer p{position:absolute;left:58px;top:42px;width:135px;font-size:6.5px;line-height:11px;color:var(--muted)}
.beer a{position:absolute;left:58px;top:78px;font-size:6.3px;color:var(--lime);text-decoration:none}

/* events */
.events{left:0;top:620px;width:717px;height:228px;background:var(--forest)}
.events .section-title{color:var(--white);top:18px;position:absolute;left:0}
.event{position:absolute;top:49px;width:134px;height:154px;border:1px solid var(--lime);background:var(--forest)}
.event .photo{width:132px;height:93px}
.event p{padding:5px 7px;font-size:7.2px;line-height:12.5px;color:#eee;height:34px}
.event .meta{position:absolute;left:0;bottom:0;width:132px;height:26px;background:var(--lime);display:flex;justify-content:space-between;align-items:center;padding:0 8px;font-size:6.8px}
.event .meta .date{color:#3e5a1f}
.event .meta .more{color:var(--forest)}

/* social */
.col-title{font-size:15px;color:var(--ink)}
.box{background:transparent;border:1px solid #d6cabd}
.fb-item{position:absolute;left:12px;width:170px}
.fb-item i{position:absolute;left:0;top:0;width:20px;height:20px;background:var(--lime);border:1px solid #3e6a1a}
.fb-item b{position:absolute;left:26px;top:0;width:145px;font-weight:400;font-size:6.3px;line-height:7px;color:var(--link)}
.fb-item small{position:absolute;left:26px;top:15px;font-size:4.8px;color:var(--muted)}
.tw-item{position:absolute;left:10px;width:165px;border-bottom:1px solid #ddd}
.tw-item i{position:absolute;left:0;top:4px;width:24px;height:24px;background:#6e9ec4}
.tw-item b{position:absolute;left:30px;top:0;font-weight:400;font-size:8px;color:#4a7fb0}
.tw-item p{position:absolute;left:30px;top:12px;width:135px;font-size:6px;line-height:9.5px;color:#444}
.tw-item small{position:absolute;left:30px;font-size:5px;color:#999}

/* footer */
.footer{left:0;top:1040px;width:717px;height:126px;background:var(--forest)}
.footer .ft{position:absolute;font-size:11.5px;color:var(--lime)}
.footer .li{position:absolute;font-size:6.8px;color:#ccc}
.bottombar{left:0;top:1166px;width:717px;height:34px;background:var(--forest-deep);text-align:center;line-height:34px;font-size:6.5px;color:#9a9a9a}
.bottombar a{color:var(--lime);text-decoration:none;margin-left:4px}
</style>
</head>
<body>

<header>
  <div class="abs topbar"></div>
  <nav class="abs nav">
    <a class="active" style="left:66px">HOME</a>
    <a style="left:127px">ABOUT US</a>
    <a style="left:192px">OUR PRODUCTS</a>
    <a style="left:277px">EVENTS</a>
    <a style="left:410px">NEWS</a>
    <a style="left:460px">BLOG</a>
    <a style="left:508px">OUR LOCATIONS</a>
    <a style="left:596px">CONTACT US</a>
  </nav>
  <div class="abs brand"><span>HARBORLINE<br>BREW CO</span></div>
</header>

<section class="abs hero" role="img" aria-label="City skyline at dusk with beer glasses and bottles">
  <div class="abs hero-product"></div>
  <p class="abs hero-title">Lorem ipsum dolor sit amet, consectetuer adipis cing elit, sed diam nonummy nibh</p>
  <p class="abs hero-sub">Ut wisi enim ad minim veniam, quis nostrud exerci tation ullamcorp er suscipit lobortis nisl ut aliquip ex ea commodo consequat.</p>
  <svg class="abs arrow" style="left:17px;top:140px" viewBox="0 0 14 28"><path d="M12 2 L2 14 L12 26" fill="none" stroke="#ccc" stroke-width="1.2"/></svg>
  <svg class="abs arrow" style="left:684px;top:140px" viewBox="0 0 14 28"><path d="M2 2 L12 14 L2 26" fill="none" stroke="#ccc" stroke-width="1.2"/></svg>
</section>

<h1 class="abs heading section-title" style="left:0;top:386px">Welcome To Harborline Brew Co</h1>
<p class="abs welcome-text">Ut wisi enim ad minim veniam, quis nostrud exerci tation ullamcorper suscipit lobortis nisl ut aliquip ex ea commodo consequat. Duis autem vel eum iriure dolor in hendrerit in vulputate velit esse molestie consequat, vel illum dolore eu feugiat nulla facilisis at vero eros et accumsan et iusto odio dignissim qui blandit praesent luptatum zzril delenit augue duis dolore te feugait nulla facilisi. Nam liber tempor cum soluta nobis eleifend option congue nihil imperdiet doming id quod mazim placerat facer possim assum.</p>

<h2 class="abs heading section-title" style="left:0;top:470px">Upcoming Beers</h2>
<svg class="abs" style="left:38px;top:540px;width:10px;height:22px" viewBox="0 0 10 22"><path d="M8 2 L2 11 L8 20" fill="none" stroke="#555" stroke-width="1.2"/></svg>
<svg class="abs" style="left:670px;top:540px;width:10px;height:22px" viewBox="0 0 10 22"><path d="M2 2 L8 11 L2 20" fill="none" stroke="#555" stroke-width="1.2"/></svg>
<div class="abs beers">
  <article class="beer" style="left:0">
    <div class="bottle" role="img" aria-label="Beer bottle"></div>
    <h3 class="heading">Ut wisi enim ad minim</h3><div class="rule"></div>
    <p>Lorem ipsum dolor sit amet, consec tetuer adipiscing elit, sed diam nonum lorem ipsum</p>
    <a>READ MORE</a>
  </article>
  <article class="beer" style="left:195px">
    <div class="bottle" role="img" aria-label="Beer bottle"></div>
    <h3 class="heading">Ut wisi enim ad minim</h3><div class="rule"></div>
    <p>Lorem ipsum dolor sit amet, consec tetuer adipiscing elit, sed diam nonum lorem ipsum</p>
    <a>READ MORE</a>
  </article>
  <article class="beer" style="left:390px">
    <div class="bottle" role="img" aria-label="Beer bottle"></div>
    <h3 class="heading">Ut wisi enim ad minim</h3><div class="rule"></div>
    <p>Lorem ipsum dolor sit amet, consec tetuer adipiscing elit, sed diam nonum lorem ipsum</p>
    <a>READ MORE</a>
  </article>
</div>

<section class="abs events">
  <h2 class="heading section-title">Events &amp; Happenings</h2>
  <article class="event" style="left:66px">
    <div class="photo" role="img" aria-label="Group of friends at a bar" style="background:linear-gradient(160deg,#5a3a2a,#231a16)"></div>
    <p>Lorem ipsum dolor sit amet, consec tetuer adipiscing elit</p>
    <div class="meta"><span class="date">OCT 14,2014</span><span class="more">READ MORE</span></div>
  </article>
  <article class="event" style="left:216px">
    <div class="photo" role="img" aria-label="Beer bottle close-up at an event" style="background:linear-gradient(160deg,#8a8f86,#2a2a26)"></div>
    <p>Ut wisi enim ad minim veniam, quis nostrud exerci tation ullamcorper</p>
    <div class="meta"><span class="date">OCT 14,2014</span><span class="more">READ MORE</span></div>
  </article>
  <article class="event" style="left:365px">
    <div class="photo" role="img" aria-label="Bartender pouring beer from a tap" style="background:linear-gradient(160deg,#b78a5e,#6a4328)"></div>
    <p>Lorem ipsum dolor sit amet, consec tetuer adipiscing elit</p>
    <div class="meta"><span class="date">OCT 14,2014</span><span class="more">READ MORE</span></div>
  </article>
  <article class="event" style="left:516px">
    <div class="photo" role="img" aria-label="Glass of amber beer beside a bottle" style="background:linear-gradient(160deg,#d9d4cf,#b07a2a 60%,#4a3320)"></div>
    <p>Ut wisi enim ad minim veniam, quis nostrud exerci tation ullamcorper</p>
    <div class="meta"><span class="date">OCT 14,2014</span><span class="more">READ MORE</span></div>
  </article>
</section>

<div class="abs" role="img" aria-label="Wheat stalks decoration" style="left:0;top:972px;width:52px;height:66px;background:linear-gradient(135deg,rgba(214,178,110,.5),rgba(214,178,110,0))"></div>
<div class="abs" role="img" aria-label="Wheat stalks decoration" style="left:665px;top:972px;width:52px;height:66px;background:linear-gradient(225deg,rgba(214,178,110,.5),rgba(214,178,110,0))"></div>

<h2 class="abs heading col-title" style="left:66px;top:864px">Circlebook</h2>
<div class="abs box" style="left:66px;top:886px;width:185px;height:128px">
  <div class="fb-item" style="top:10px"><i></i><b>Lorem ipsum dolor sit amet, consectetuer adipiscing  sed diam nonummy nibh</b><small>6 people recommend this.</small></div>
  <div class="fb-item" style="top:41px"><i></i><b>Lorem ipsum dolor sit amet, consectetuer adipiscing  sed diam nonummy nibh</b><small>6 people recommend this.</small></div>
  <div class="fb-item" style="top:72px"><i></i><b>Lorem ipsum dolor sit amet, consectetuer adipiscing  sed diam nonummy nibh</b><small>6 people recommend this.</small></div>
  <div class="abs" style="left:14px;top:106px;width:8px;height:8px;background:#3b5a99"></div>
  <span class="abs" style="left:26px;top:106px;font-size:5px;color:#666">Circlebook social plugin</span>
</div>

<h2 class="abs heading col-title" style="left:265px;top:864px">Chirper</h2>
<div class="abs box" style="left:266px;top:886px;width:184px;height:128px">
  <div class="tw-item" style="top:8px;height:40px"><i></i><b>Harborline Brew Co</b><p>Ut wisi enim ad minim veniam, quis nostrud exerci tation ullamcorper</p><small style="top:31px">7 Jun</small></div>
  <div class="tw-item" style="top:50px;height:38px"><i></i><b>Harborline Brew Co</b><p>Ut wisi enim ad minim veniam..</p><small style="top:24px">7 Jun</small></div>
  <div class="tw-item" style="top:88px;height:38px;border-bottom:none"><i></i><b>Harborline Brew Co</b><p>Typi non habent claritatem insitam;</p><small style="top:24px">7 Jun</small></div>
</div>

<div class="abs" style="left:466px;top:869px;width:185px;height:25px;background:var(--lime)"></div>
<h2 class="abs heading" style="left:478px;top:874px;font-size:12px;color:var(--forest)">Upcoming Events</h2>
<div class="abs" role="img" aria-label="Friends gathered at a bar event" style="left:466px;top:894px;width:185px;height:120px;background:linear-gradient(160deg,#6a4a34,#2a1e18)"></div>

<footer class="abs footer">
  <svg class="abs" style="left:69px;top:34px;width:7px;height:9px" viewBox="0 0 7 9"><path d="M3.5 9 C1 5.5 0 4.5 0 3.3 A3.5 3.5 0 0 1 7 3.3 C7 4.5 6 5.5 3.5 9Z" fill="#8dc63f"/><circle cx="3.5" cy="3.3" r="1.2" fill="#1b2a1a"/></svg>
  <span class="li" style="left:80px;top:34px;color:#eee">CITY NAME</span>
  <span class="li" style="left:80px;top:46px;line-height:12px">361 lorem Ipsm.lorem Ipsm<br>lorem Ipsm lorem 12768</span>
  <svg class="abs" style="left:66px;top:72px;width:9px;height:7px" viewBox="0 0 9 7"><rect width="9" height="7" fill="#8dc63f"/><path d="M0 0 L4.5 4 L9 0" fill="none" stroke="#1b2a1a" stroke-width=".8"/></svg>
  <span class="li" style="left:81px;top:70px;font-size:7.5px">info@domainname.com</span>
  <svg class="abs" style="left:66px;top:93px;width:9px;height:9px" viewBox="0 0 9 9"><rect width="9" height="9" rx="1.5" fill="#8dc63f"/><path d="M2.5 2 L3.8 2 L4.2 3.5 L3.5 4 Q4.2 5.3 5 5.6 L5.6 5 L7 5.4 L7 6.6 Q4 7.2 2.5 2Z" fill="#1b2a1a"/></svg>
  <span class="li" style="left:82px;top:92px;font-size:7.5px">+1.234.567.78900</span>

  <span class="ft heading" style="left:234px;top:16px">Quick Links</span>
  <span class="li" style="left:235px;top:37px">Home</span>
  <span class="li" style="left:235px;top:52px">Services</span>
  <span class="li" style="left:235px;top:68px">Products</span>
  <span class="li" style="left:235px;top:83px">About Us</span>
  <span class="li" style="left:235px;top:98px">Contact Us</span>

  <span class="ft heading" style="left:350px;top:16px">Social Networks</span>
  <div class="abs" style="left:352px;top:38px;width:7px;height:7px;background:#3b5a99"></div><span class="li" style="left:362px;top:37px">Circlebook</span>
  <div class="abs" style="left:352px;top:53px;width:7px;height:7px;background:#4a9ad4"></div><span class="li" style="left:362px;top:52px">Chirper</span>
  <div class="abs" style="left:352px;top:69px;width:7px;height:7px;background:#1e6fa8"></div><span class="li" style="left:362px;top:68px">ProLink</span>
  <div class="abs" style="left:352px;top:84px;width:7px;height:7px;background:#d34836"></div><span class="li" style="left:362px;top:83px">Searchly+</span>
  <div class="abs" style="left:352px;top:99px;width:7px;height:7px;background:#e8731e"></div><span class="li" style="left:362px;top:98px">RSS</span>

  <span class="ft heading" style="left:492px;top:16px">Newsletter Signup</span>
  <span class="li" style="left:493px;top:36px;width:170px;line-height:12px;color:#999">Enter your email address to receive our latest newsletters containing our latest News.</span>
  <div class="abs" style="left:493px;top:61px;width:157px;height:23px;background:var(--white)"></div>
  <span class="li" style="left:502px;top:69px;color:#999">Email Address</span>
  <div class="abs" style="left:493px;top:88px;width:70px;height:20px;background:var(--lime);text-align:center;line-height:20px;font-size:6.5px;color:var(--forest)">SUBSCRIBE</div>
</footer>

<div class="abs bottombar">©2014 Harborline Brew Co. <a>Privacy Policy</a> <a style="margin-left:8px">Terms of Service</a></div>

</body>
</html>
```